VELMOR Website Design

We need a website designed for our company VELMOR. We are a luxury lifestyle club that will provide benefits and services for our members. The site should be clean & sleek, preferably using black and white (or darker colors). (example sites: stravenhall.example, plinth.example)

Here is a link of a sample page I did using wix. (https://dunmere7.sitehostly.example/mysite) This can be used to get a general idea.

Target Market(s)

Upper Middle Class in the United States

Number of Pages Required

5+ page

Font styles to use
Sans Serif
Other font styles liked:
• Arial (or other similar fonts)

Requirements
Must have
• A clean design that is eye-catching and speaks to our company.
Nice to have
• Ideas for copy.

```html
<!DOCTYPE html>
<html lang="en">
<head>
<meta charset="utf-8">
<title>VELMOR — Members Only Lifestyle Club</title>
<link rel="stylesheet" href="https://fonts.googleapis.com/css2?family=Montserrat:wght@500;600;700;800&family=Open+Sans:wght@400;600&display=swap">
<style>
:root{
  --black:#000;
  --ink:#1a1a1a;
  --text:#333;
  --muted:#555;
  --white:#fff;
  --band:#f3f0f0;
  --line:#d8d8d8;
  --icon:#3a3a3a;
  --social:#1d3f8f;
  --social-alt:#1da1f2;
  --social-dark:#10255e;
}
*{margin:0;padding:0;box-sizing:border-box}
html,body{width:1200px;height:3358px;overflow:hidden}
body{position:relative;background:var(--white);font-family:"Open Sans",Arial,sans-serif;color:var(--text)}
.abs{position:absolute}
.heading{font-family:"Montserrat",Arial,sans-serif}

/* Hero */
.hero{left:0;top:0;width:1200px;height:656px;
  background:radial-gradient(circle at 78% 22%,#ff2e9a 0,rgba(255,46,154,0) 22%),
             radial-gradient(circle at 35% 35%,#6d3a8e 0,rgba(109,58,142,0) 40%),
             radial-gradient(circle at 60% 70%,#3a2130 0,rgba(58,33,48,0) 45%),
             linear-gradient(180deg,#1a1020 0%,#2a1824 55%,#120a10 100%)}
.brand{left:45px;top:20px;font-family:"Montserrat",Arial,sans-serif;font-weight:800;font-size:36px;color:var(--white);letter-spacing:1px}
.nav{top:20px;right:40px;display:flex;align-items:center;gap:26px;font-family:"Montserrat",Arial,sans-serif;font-weight:700;font-size:13px;color:var(--white)}
.nav a{color:inherit;text-decoration:none}
.nav .current{background:var(--white);color:var(--black);padding:6px 12px}
.nav .apply{border:2px solid var(--white);padding:5px 12px}
.dots{left:560px;top:594px;display:flex;gap:16px}
.dots span{width:8px;height:8px;border-radius:50%;background:rgba(255,255,255,.55)}
.dots span.on{background:var(--white)}

/* Intro band */
.intro{left:0;top:656px;width:1200px;height:345px;background:var(--band)}
.rule{height:3px;background:var(--black)}
.welcome{left:123px;top:705px}
.welcome .rule{width:46px}
.welcome .eyebrow{margin-top:22px;font-family:"Montserrat",Arial,sans-serif;font-weight:500;font-size:14px;color:var(--black)}
.welcome .name{font-family:"Montserrat",Arial,sans-serif;font-weight:800;font-size:42px;color:var(--black);line-height:1.05;margin-top:4px}
.welcome p{width:230px;font-size:13px;line-height:1.5;color:var(--text);margin-top:20px}
.welcome p+p{margin-top:12px}
.stats{left:448px;top:700px;width:290px;height:260px}
.stats .vline{left:110px;top:0;width:1px;height:260px;background:var(--line)}
.stats .hline{left:0;top:128px;width:290px;height:1px;background:var(--line)}
.stat{width:130px}
.stat .ico{width:32px;height:32px;border-radius:50%;background:var(--ink);display:flex;align-items:center;justify-content:center}
.stat .num{font-family:"Montserrat",Arial,sans-serif;font-weight:500;font-size:30px;color:var(--black);margin-top:10px;line-height:1}
.stat .label{font-family:"Montserrat",Arial,sans-serif;font-weight:600;font-size:12px;color:var(--black);margin-top:8px}
.card{left:772px;top:593px;width:298px;height:410px;background:var(--white);box-shadow:0 6px 24px rgba(0,0,0,.12);text-align:center}
.card .rule{width:44px;height:2px;margin:107px auto 0}
.card h2{font-family:"Montserrat",Arial,sans-serif;font-weight:500;font-size:24px;color:var(--black);line-height:1.35;margin-top:30px}
.btn-dark{display:inline-block;background:var(--black);color:var(--white);font-family:"Montserrat",Arial,sans-serif;font-weight:700;font-size:15px;padding:12px 32px;margin-top:34px}

/* Services */
.services-head{left:0;top:1070px;width:1200px;text-align:center}
.services-head .rule{width:46px;margin:0 auto}
.services-head h2{font-family:"Montserrat",Arial,sans-serif;font-weight:700;font-size:26px;color:var(--black);margin-top:16px}
.grid{left:235px;top:1164px;display:grid;grid-template-columns:repeat(3,224px);grid-auto-rows:208px;column-gap:30px;row-gap:30px}
.tile{background:var(--white);box-shadow:0 2px 12px rgba(0,0,0,.12);display:flex;flex-direction:column;align-items:center;padding-top:44px}
.tile svg{width:54px;height:54px;fill:var(--icon)}
.tile .dash{width:38px;height:1px;background:#777;margin-top:30px}
.tile .title{font-family:"Montserrat",Arial,sans-serif;font-weight:600;font-size:14px;color:var(--ink);margin-top:20px}
.tile.featured{background:var(--black)}
.tile.featured svg{fill:var(--white)}
.tile.featured .dash{background:var(--white)}
.tile.featured .title{color:var(--white)}

/* Feature band */
.feature{left:0;top:1923px;width:1200px;height:1077px;background:var(--black)}
.photo-experiences{left:130px;top:2017px;width:530px;height:401px;background:radial-gradient(circle at 25% 20%,#c97a2a 0,rgba(201,122,42,0) 35%),linear-gradient(135deg,#5a3520 0%,#2b1a12 60%,#140c08 100%)}
.photo-benefits{left:540px;top:2517px;width:530px;height:403px;background:radial-gradient(circle at 60% 15%,#e3b060 0,rgba(227,176,96,0) 40%),linear-gradient(160deg,#6b4a28 0%,#3a2a1a 55%,#1c150e 100%)}
.copy{color:var(--white)}
.copy .rule{width:96px;height:3px;background:var(--white)}
.copy h3{font-family:"Montserrat",Arial,sans-serif;font-weight:700;font-size:26px;margin-top:16px}
.copy p{font-size:13.5px;line-height:1.5;margin-top:14px;width:360px}
.copy p+p{margin-top:20px}
.btn-light{display:inline-block;background:var(--white);color:var(--black);font-family:"Montserrat",Arial,sans-serif;font-weight:700;font-size:15px;padding:12px 22px;margin-top:34px}
.copy-experiences{left:717px;top:2056px}
.copy-benefits{left:134px;top:2557px}

/* Footer */
.footer-brand{left:132px;top:3096px;font-family:"Montserrat",Arial,sans-serif;font-weight:800;font-size:42px;color:var(--black)}
.fcol{top:3050px;font-size:11.5px;color:var(--text)}
.fcol h4{font-family:"Montserrat",Arial,sans-serif;font-weight:700;font-size:12px;color:var(--black);margin-bottom:24px}
.contact-col{left:446px}
.contact-col .row{display:flex;gap:14px;align-items:flex-start;line-height:1.45;margin-bottom:20px}
.contact-col svg{width:12px;height:12px;fill:var(--ink);flex:none;margin-top:2px}
.menu-col{left:705px}
.menu-col li{list-style:none;line-height:1.6}
.social-col{left:938px}
.social-col .row{display:flex;align-items:center;gap:14px;margin-bottom:14px}
.social-col .dot{width:26px;height:26px;border-radius:50%;background:var(--social)}
.social-col .dot.alt{background:var(--social-alt)}
.social-col .dot.dark{background:var(--social-dark)}
.footer-line{left:130px;top:3265px;width:940px;height:1px;background:var(--line)}
.copyright{left:0;top:3312px;width:1200px;text-align:center;font-size:11px;color:var(--text)}
</style>
</head>
<body>

<header>
  <div class="abs hero" role="img" aria-label="Party photo: guests celebrating under confetti and pink stage lights"></div>
  <div class="abs brand">VELMOR</div>
  <nav class="abs nav">
    <a class="current" href="#">HOME</a>
    <a href="#">ABOUT</a>
    <a href="#">SERVICES AND BENEFITS</a>
    <a href="#">CONTACT US</a>
    <a class="apply" href="#">APPLY</a>
  </nav>
  <div class="abs dots"><span></span><span class="on"></span><span></span><span></span></div>
</header>

<section>
  <div class="abs intro"></div>
  <div class="abs welcome">
    <div class="rule"></div>
    <div class="eyebrow">WELCOME TO</div>
    <div class="name">VELMOR</div>
    <p>VELMOR is a members only lifestyle club founded in order to bring the best services, experiences, and opportunities to our diverse community of members.</p>
    <p>Our members consist of creatives, athletes, artists, and other professionals.</p>
  </div>

  <div class="abs stats">
    <div class="abs vline"></div>
    <div class="abs hline"></div>
    <div class="abs stat" style="left:0;top:5px">
      <div class="ico"><svg width="16" height="16" viewBox="0 0 16 16" fill="#fff"><rect x="2" y="3" width="12" height="11" rx="1"/><rect x="3.5" y="6.5" width="9" height="6" fill="#1a1a1a"/><rect x="4.5" y="1.5" width="1.6" height="3"/><rect x="9.9" y="1.5" width="1.6" height="3"/></svg></div>
      <div class="num">6</div><div class="label">EVENTS</div>
    </div>
    <div class="abs stat" style="left:148px;top:5px">
      <div class="ico"><svg width="18" height="16" viewBox="0 0 18 16" fill="#fff"><circle cx="9" cy="5" r="3"/><circle cx="3.8" cy="6.5" r="2"/><circle cx="14.2" cy="6.5" r="2"/><path d="M4 14a5 5 0 0 1 10 0z"/><path d="M0 14a3.8 3.8 0 0 1 5-3.6 6 6 0 0 0-1.3 3.6z"/><path d="M18 14a3.8 3.8 0 0 0-5-3.6 6 6 0 0 1 1.3 3.6z"/></svg></div>
      <div class="num">35</div><div class="label">MEMBERS</div>
    </div>
    <div class="abs stat" style="left:0;top:158px">
      <div class="ico"><svg width="16" height="16" viewBox="0 0 16 16" fill="#fff"><rect x="1.5" y="4.5" width="13" height="9" rx="1"/><rect x="5.5" y="2" width="5" height="3" fill="none" stroke="#fff" stroke-width="1.4"/><rect x="1.5" y="8" width="13" height="1" fill="#1a1a1a"/></svg></div>
      <div class="num">35</div><div class="label">PROJECTS</div>
    </div>
    <div class="abs stat" style="left:148px;top:158px">
      <div class="ico"><svg width="16" height="16" viewBox="0 0 16 16"><rect x="2" y="3" width="10" height="11" fill="none" stroke="#fff" stroke-width="1.4"/><path d="M7 10l6-6 1.5 1.5-6 6H7z" fill="#fff"/></svg></div>
      <div class="num">12</div><div class="label">YEARS EXPERIENCE</div>
    </div>
  </div>

  <div class="abs card">
    <div class="rule"></div>
    <h2>A Members<br>Only Lifestyle Club</h2>
    <a class="btn-dark">APPLY</a>
  </div>
</section>

<section>
  <div class="abs services-head">
    <div class="rule"></div>
    <h2>SERVICES</h2>
  </div>
  <div class="abs grid">
    <div class="tile">
      <svg viewBox="0 0 48 48"><path d="M6 9h36v33H6zM9 17v22h30V17z"/><rect x="13" y="5" width="3" height="8"/><rect x="32" y="5" width="3" height="8"/><g><rect x="12" y="20" width="5" height="4"/><rect x="19" y="20" width="5" height="4"/><rect x="26" y="20" width="5" height="4"/><rect x="33" y="20" width="3" height="4"/><rect x="12" y="27" width="5" height="4"/><rect x="19" y="27" width="5" height="4"/><rect x="26" y="27" width="5" height="4"/><rect x="12" y="33" width="5" height="4"/><rect x="19" y="33" width="5" height="4"/></g></svg>
      <div class="dash"></div><div class="title">Accounting</div>
    </div>
    <div class="tile">
      <svg viewBox="0 0 48 48"><circle cx="30" cy="14" r="10" fill="none" stroke="#3a3a3a" stroke-width="2"/><path d="M31 8v12M27.5 11h5a2 2 0 0 1 0 4h-5M27.5 15h5a2 2 0 0 1 0 4h-5" fill="none" stroke="#3a3a3a" stroke-width="1.8"/><path d="M4 30h6v14H4zM12 32c6-2 10-1 14 1h8c2 0 2 3 0 3h-9l1 1h10l8-5c2-1 4 1 2 3l-10 8H12z"/></svg>
      <div class="dash"></div><div class="title">Investment</div>
    </div>
    <div class="tile">
      <svg viewBox="0 0 48 48"><circle cx="24" cy="14" r="9"/><path d="M6 46c0-10 8-16 18-16s18 6 18 16z"/><path d="M22 30h4l1 3-2 9h-2l-2-9z" fill="#fff"/></svg>
      <div class="dash"></div><div class="title">Lawyer</div>
    </div>
    <div class="tile">
      <svg viewBox="0 0 48 48"><path d="M8 6h20v38H8zM30 18h12v26H30z"/><g fill="#fff"><rect x="12" y="10" width="4" height="4"/><rect x="20" y="10" width="4" height="4"/><rect x="12" y="18" width="4" height="4"/><rect x="20" y="18" width="4" height="4"/><rect x="12" y="26" width="4" height="4"/><rect x="20" y="26" width="4" height="4"/><rect x="15" y="36" width="6" height="8"/><rect x="34" y="22" width="4" height="4"/><rect x="34" y="30" width="4" height="4"/></g></svg>
      <div class="dash"></div><div class="title">Real Estate</div>
    </div>
    <div class="tile featured">
      <svg viewBox="0 0 48 48"><circle cx="28" cy="22" r="15" fill="none" stroke="#fff" stroke-width="3"/><path d="M6 14c2-3 5-3 6-1l3 5c1 2 0 3-2 4 1 4 4 8 8 10 1-2 2-3 4-2l5 3c2 1 2 4-1 6-6 4-14-1-19-7S3 19 6 14z"/><text x="28" y="27" text-anchor="middle" font-family="Montserrat,Arial,sans-serif" font-weight="800" font-size="13" fill="#fff">24</text></svg>
      <div class="dash"></div><div class="title">24/7 Concierge</div>
    </div>
    <div class="tile">
      <svg viewBox="0 0 48 48"><path d="M4 22h14L10 8h5l12 14h12c4 0 6 2 6 2s-2 2-6 2H27L15 40h-5l8-14H4l-2-2z"/></svg>
      <div class="dash"></div><div class="title">Private Jet Travel</div>
    </div>
    <div class="tile">
      <svg viewBox="0 0 48 48"><path d="M4 8h38v20h-3V16H7v24h22v3H4z"/><g><rect x="9" y="4" width="2" height="7"/><rect x="15" y="4" width="2" height="7"/><rect x="21" y="4" width="2" height="7"/><rect x="27" y="4" width="2" height="7"/><rect x="33" y="4" width="2" height="7"/><rect x="10" y="20" width="4" height="3"/><rect x="17" y="20" width="4" height="3"/><rect x="24" y="20" width="4" height="3"/><rect x="31" y="20" width="4" height="3"/><rect x="10" y="27" width="4" height="3"/><rect x="17" y="27" width="4" height="3"/><rect x="10" y="34" width="4" height="3"/><rect x="17" y="34" width="4" height="3"/></g><circle cx="38" cy="37" r="8"/><path d="M34 37l3 3 5-6" fill="none" stroke="#fff" stroke-width="2"/></svg>
      <div class="dash"></div><div class="title">Event Access</div>
    </div>
    <div class="tile">
      <svg viewBox="0 0 48 48"><path d="M4 8h34v16h-3v-8H7v24h20v3H4z"/><rect x="10" y="4" width="3" height="8"/><rect x="29" y="4" width="3" height="8"/><rect x="28" y="30" width="18" height="14" rx="2"/><path d="M31 30v-4a6 6 0 0 1 12 0v4" fill="none" stroke="#3a3a3a" stroke-width="3"/><circle cx="37" cy="37" r="2" fill="#fff"/></svg>
      <div class="dash"></div><div class="title">Private Events</div>
    </div>
    <div class="tile">
      <svg viewBox="0 0 48 48"><path d="M4 14h40v28H4z"/><path d="M17 14V9h14v5" fill="none" stroke="#3a3a3a" stroke-width="3"/><rect x="4" y="25" width="40" height="2" fill="#fff"/><rect x="21" y="23" width="6" height="6"/></svg>
      <div class="dash"></div><div class="title">Experiences</div>
    </div>
  </div>
</section>

<section>
  <div class="abs feature"></div>
  <div class="abs photo-experiences" role="img" aria-label="Photo: friends toasting with glasses of rosé at a bar with warm bokeh lights"></div>
  <div class="abs copy copy-experiences">
    <div class="rule"></div>
    <h3>EXPERIENCES</h3>
    <p>VELMOR organizes and supports a ton of private events and parties for our members.</p>
    <p>Members are also provided access to exclusive venues and events from our partners.</p>
    <p>Network with other members to build lasting relationships.</p>
    <a class="btn-light">READ MORE</a>
  </div>
  <div class="abs copy copy-benefits">
    <div class="rule"></div>
    <h3>BENEFITS</h3>
    <p>VELMOR organizes and supports a ton of private events and parties for our members.</p>
    <p>Members are also provided access to exclusive venues and events from our partners.</p>
    <p>Network with other members to build lasting relationships.</p>
    <a class="btn-light">READ MORE</a>
  </div>
  <div class="abs photo-benefits" role="img" aria-label="Photo: guests raising champagne glasses at a candlelit dinner under string lights"></div>
</section>

<footer>
  <div class="abs footer-brand">VELMOR</div>
  <div class="abs fcol contact-col">
    <h4>CONTACT US</h4>
    <div class="row"><svg viewBox="0 0 12 12"><path d="M6 0a4 4 0 0 1 4 4c0 3-4 8-4 8S2 7 2 4a4 4 0 0 1 4-4zm0 2.5a1.5 1.5 0 1 0 0 3 1.5 1.5 0 0 0 0-3z"/></svg><span>72 Larkfield Row<br>Ashcombe, IL 60999</span></div>
    <div class="row"><svg viewBox="0 0 12 12"><path d="M1.5 1.5c1-1 2-1 2.5 0l1 2c.4.8 0 1.3-.7 1.8.6 1.2 1.4 2 2.6 2.6.5-.7 1-1.1 1.8-.7l2 1c1 .5 1 1.5 0 2.5-3 2-10-5-9.2-9.2z"/></svg><span>555.014.2210</span></div>
    <div class="row"><svg viewBox="0 0 12 12"><path d="M0 2h12v8H0z"/><path d="M0 2l6 5 6-5" fill="none" stroke="#fff" stroke-width="1"/></svg><span>info@velmor.example</span></div>
  </div>
  <div class="abs fcol menu-col">
    <h4>MENU</h4>
    <ul><li>Home</li><li>About</li><li>Services and Benefits</li><li>Contact Us</li><li>Apply</li></ul>
  </div>
  <div class="abs fcol social-col">
    <h4>CONNECT WITH US</h4>
    <div class="row"><span class="dot"></span><span>Gatherly</span></div>
    <div class="row"><span class="dot alt"></span><span>Chirpline</span></div>
    <div class="row"><span class="dot dark"></span><span>Careerlink</span></div>
  </div>
  <div class="abs footer-line"></div>
  <div class="abs copyright">Copyrights @ 2018 All Rights Reserved</div>
</footer>

</body>
</html>
```